Corporate Travel Technology Company needs new Business Card design

We need a new business card design to reflect our re-branded company. Our company is called tolven (pronounced tolvenn) and we provide Business Intelligence and Smart Corporate Trip Control solutions for the corporate travel industry. Our multinational customers use our solutions to manage large travel budgets and frequent travellers, as well as to save money and reduce risk. We'd like to see designs that use the blue and green palette as well as our corporate logo (attached below). The design should communicate innovation, insight, forward thinking, contemporary, trusted.

Target Market(s)

Large multinational corporates and Travel Agencies.

Industry/Entity Type

Business

Contact Information for Business Card

Rosalind Mercer
Chief Executive
tolven
Phone number - +61 (0)2 8134 2907
Email address - rosalind.mercer@tolven-example.com
Mobile number - +61 (0)438 516 702
www.tolven-example.com

Font styles to use
Other font styles liked:
• Please use font as close to corporate logo as possible

Colors
0255a3
0393ce
00a990
33b8a4
33a6d7
3176b5

Requirements
Must have
• Please include the words;
• Smart Corporate Trip Control
• Sharper Insight for Every Business Journey
• Use corporate logo - although icon can be stylised if needed

```html
<!DOCTYPE html>
<html lang="en">
<head>
<meta charset="utf-8">
<title>tolven business card</title>
<link rel="stylesheet" href="https://fonts.googleapis.com/css2?family=Open+Sans:wght@400;600;700&display=swap">
<style>
  :root {
    --stage: #2b2d31;
    --brand-blue: #3176b5;
    --brand-blue-soft: #d6e6f4;
    --ink-slate: #3f5256;
    --ink-dark: #333a3d;
    --paper: #ffffff;
  }
  html, body {
    margin: 0;
    padding: 0;
    width: 1200px;
    height: 864px;
    overflow: hidden;
    background: var(--stage);
    font-family: "Open Sans", Arial, sans-serif;
  }
  .canvas {
    position: relative;
    width: 1200px;
    height: 864px;
  }
  .card {
    position: absolute;
    width: 600px;
    height: 343px;
    box-sizing: border-box;
    overflow: hidden;
  }
  .card-back {
    left: 300px;
    top: 50px;
    background: var(--brand-blue);
    color: var(--paper);
    text-align: center;
  }
  .card-back .wordmark {
    margin: 110px 0 0;
    font-size: 64px;
    font-weight: 400;
    line-height: 1;
    letter-spacing: 1px;
  }
  .card-back .taglines {
    margin: 34px 0 0;
    font-size: 15px;
    font-weight: 700;
    line-height: 1.3;
  }
  .card-front {
    left: 300px;
    top: 460px;
    background: var(--paper);
  }
  .card-front .wordmark {
    position: absolute;
    left: 44px;
    top: 36px;
    margin: 0;
    font-size: 50px;
    font-weight: 400;
    line-height: 1;
    color: var(--ink-slate);
    letter-spacing: 1px;
  }
  .decor-disc {
    position: absolute;
    left: 352px;
    top: 40px;
    width: 300px;
    height: 300px;
    border-radius: 50%;
    background: var(--brand-blue-soft);
  }
  .person {
    position: absolute;
    left: 44px;
    top: 122px;
  }
  .person .name {
    margin: 0;
    font-size: 18px;
    font-weight: 700;
    color: var(--brand-blue);
  }
  .person .role {
    margin: 2px 0 0;
    font-size: 13px;
    color: var(--ink-dark);
  }
  .contacts {
    position: absolute;
    left: 40px;
    top: 200px;
    margin: 0;
    padding: 0;
    list-style: none;
    font-size: 13.5px;
    color: var(--ink-dark);
  }
  .contacts li {
    display: flex;
    align-items: center;
    gap: 8px;
    height: 21px;
  }
  .contacts svg {
    width: 12px;
    height: 12px;
    fill: var(--brand-blue);
    flex: none;
  }
</style>
</head>
<body>
<main class="canvas">
  <section class="card card-back" aria-label="Card back">
    <p class="wordmark">tolven</p>
    <p class="taglines">Smart Corporate Trip Control<br>Sharper Insight for Every Business Journey</p>
  </section>

  <section class="card card-front" aria-label="Card front">
    <div class="decor-disc"></div>
    <p class="wordmark">tolven</p>
    <div class="person">
      <p class="name">Rosalind Mercer</p>
      <p class="role">Chief Executive</p>
    </div>
    <ul class="contacts">
      <li>
        <svg viewBox="0 0 12 12" aria-hidden="true"><path d="M2.5 0.5 L4.5 0.5 L5 3 L3.6 4 Q4.6 6.6 7.8 8.2 L8.8 6.9 L11.4 7.5 L11.4 9.6 Q11 11.5 9 11.4 Q1 10.5 0.6 2.4 Q0.6 0.6 2.5 0.5 Z"/></svg>
        <span>+61 (0)2 8134 2907</span>
      </li>
      <li>
        <svg viewBox="0 0 12 12" aria-hidden="true"><path d="M3 0 H9 A1 1 0 0 1 10 1 V11 A1 1 0 0 1 9 12 H3 A1 1 0 0 1 2 11 V1 A1 1 0 0 1 3 0 Z M3.2 1.5 V8.5 H8.8 V1.5 Z M5.2 9.6 V10.8 H6.8 V9.6 Z"/></svg>
        <span>+61 (0)438 516 702</span>
      </li>
      <li>
        <svg viewBox="0 0 12 12" aria-hidden="true"><path d="M0 2 H12 V10 H0 Z M1 3 L6 6.8 L11 3 V2.8 H1 Z" fill-rule="evenodd"/></svg>
        <span>rosalind.mercer@tolven-example.com</span>
      </li>
      <li>
        <svg viewBox="0 0 12 12" aria-hidden="true"><path d="M5 3 L7 1 A2.5 2.5 0 0 1 11 5 L9 7 L8 6 L10 4 A1.2 1.2 0 0 0 8 2 L6 4 Z M7 9 L5 11 A2.5 2.5 0 0 1 1 7 L3 5 L4 6 L2 8 A1.2 1.2 0 0 0 4 10 L6 8 Z M3.8 7.4 L7.4 3.8 L8.2 4.6 L4.6 8.2 Z"/></svg>
        <span>www.tolven-example.com</span>
      </li>
    </ul>
  </section>
</main>
</body>
</html>
```